IT solutions & services company requires stationary makeover

Looking for a consistent modern, professional design across our printed client touch points:
Business Cards
Letterhead
Client proposal
Flyer
Postcard

We provide solutions for SME IT - servers, backups, AV etc, and the ongoing services around them.
we are happy with our logo - please see attached and would like the colour theme to be maintained.

```html
<!DOCTYPE html>
<html lang="en">
<head>
<meta charset="utf-8">
<title>nexa – Letterhead</title>
<link rel="stylesheet" href="https://fonts.googleapis.com/css2?family=Arimo:ital,wght@0,400;0,700;1,400;1,700&display=swap">
<style>
  :root {
    --brand-blue: #1ea6df;
    --ink-dark: #2b2424;
    --paper: #ffffff;
    --backdrop: #e9e7e4;
    --contact-ink: #1f1f1f;
  }
  * { margin: 0; padding: 0; box-sizing: border-box; }
  html, body {
    width: 1055px;
    height: 1200px;
    overflow: hidden;
    background: var(--backdrop);
  }
  .canvas {
    position: relative;
    width: 1055px;
    height: 1200px;
    display: flex;
    align-items: center;
    justify-content: center;
  }
  .letterhead {
    width: 806px;
    height: 1140px;
    background: var(--paper);
    box-shadow: 0 2px 10px rgba(0,0,0,0.12);
    position: relative;
  }
  .letterhead-header {
    height: 160px;
    background: var(--brand-blue);
    display: flex;
    justify-content: space-between;
    align-items: center;
    padding: 0 30px 0 70px;
  }
  .brand {
    display: flex;
    align-items: center;
    gap: 14px;
  }
  .brand-dot {
    width: 44px;
    height: 44px;
    border-radius: 50%;
    background: var(--ink-dark);
  }
  .brand-name {
    font-family: 'Arimo', Arial, sans-serif;
    font-weight: 400;
    font-size: 62px;
    line-height: 1;
    color: var(--ink-dark);
    letter-spacing: 1px;
  }
  .contact {
    font-family: 'Arimo', Arial, sans-serif;
    font-style: italic;
    font-size: 13px;
    line-height: 1.45;
    color: var(--contact-ink);
    text-align: right;
    list-style: none;
  }
  .contact .contact-web {
    font-weight: 700;
    color: var(--paper);
  }
</style>
</head>
<body>
<main class="canvas">
  <article class="letterhead">
    <header class="letterhead-header">
      <div class="brand">
        <span class="brand-dot" aria-hidden="true"></span>
        <span class="brand-name">nexa</span>
      </div>
      <ul class="contact">
        <li>03 555 0182</li>
        <li>jlee@nexa-it.example</li>
        <li>Level 1,</li>
        <li>Harbour Lane,</li>
        <li>Christchurch, NZ</li>
        <li class="contact-web">www.nexa-it.example</li>
      </ul>
    </header>
  </article>
</main>
</body>
</html>
```